Residential Remodeling Contractor needs updated business card

I need a new design for my business card.
Name of the company is Ridgefell Construction. I need a card that commands presence, strength, integrity. I have been in business for 28 years. I am a Residential Remodeling Contractor that covers all aspects of a residential remodel and build.

```html
<!DOCTYPE html>
<html lang="en">
<head>
<meta charset="utf-8">
<title>Ridgefell Construction – Business Card</title>
<link href="https://fonts.googleapis.com/css2?family=Montserrat:wght@400;600&display=swap" rel="stylesheet">
<style>
  :root {
    --card-blue: #213f86;
    --ink-white: #ffffff;
    --ink-soft: #dfe5f3;
    --rule: rgba(255, 255, 255, 0.45);
    --backdrop: #2d2824;
  }
  * { box-sizing: border-box; margin: 0; padding: 0; }
  html, body {
    width: 1200px; height: 786px; overflow: hidden;
    background: var(--backdrop);
  }
  .canvas {
    position: relative; width: 1200px; height: 786px;
    display: flex; align-items: center; justify-content: center; gap: 40px;
  }
  .card {
    position: relative; width: 540px; height: 309px;
    background: var(--card-blue); color: var(--ink-white);
    box-shadow: 0 10px 24px rgba(0,0,0,0.45);
    font-family: "Montserrat", sans-serif;
  }

  /* Company name set in the card's text face */
  .company-name {
    position: absolute;
    display: flex; align-items: center; gap: 10px;
    font-weight: 600; color: var(--ink-white);
    line-height: 1; white-space: nowrap;
  }
  .company-mark {
    flex: none; background: var(--ink-white);
  }

  /* Contact side */
  .card-back .company-name {
    left: 34px; top: 146px; font-size: 15px;
  }
  .card-back .company-mark { width: 10px; height: 10px; }
  .divider {
    position: absolute; left: 244px; top: 68px; width: 1px; height: 178px;
    background: var(--rule);
  }
  .contact {
    position: absolute; left: 266px; top: 66px;
  }
  .contact-name { font-weight: 600; font-size: 17px; letter-spacing: 0.2px; }
  .contact-role { font-size: 10px; color: var(--ink-soft); margin-top: 3px; }
  .contact-address { font-size: 11px; line-height: 1.35; margin-top: 18px; }
  .contact-list { list-style: none; margin-top: 14px; }
  .contact-list li {
    display: flex; align-items: center; gap: 10px;
    font-size: 11px; line-height: 1; margin-bottom: 9px;
  }
  .contact-list svg { width: 12px; height: 12px; flex: none; }

  /* Name side */
  .card-front .company-name {
    right: 44px; top: 140px; font-size: 26px; gap: 14px;
  }
  .card-front .company-mark { width: 18px; height: 18px; }
</style>
</head>
<body>
<main class="canvas">

  <section class="card card-back" aria-label="Business card, contact side">
    <p class="company-name"><span class="company-mark" aria-hidden="true"></span>Ridgefell Construction</p>
    <div class="divider"></div>
    <div class="contact">
      <p class="contact-name">Daniel Harlow</p>
      <p class="contact-role">Owner</p>
      <p class="contact-address">48 Cedar Hollow Road<br>Brandon, MS 39042</p>
      <ul class="contact-list">
        <li>
          <svg viewBox="0 0 24 24" aria-hidden="true"><path fill="#fff" d="M6.6 10.8a15 15 0 0 0 6.6 6.6l2.2-2.2a1 1 0 0 1 1-.25 11.4 11.4 0 0 0 3.6.57 1 1 0 0 1 1 1V20a1 1 0 0 1-1 1A17 17 0 0 1 3 4a1 1 0 0 1 1-1h3.5a1 1 0 0 1 1 1c0 1.25.2 2.45.57 3.57a1 1 0 0 1-.25 1z"/></svg>
          555.014.2290
        </li>
        <li>
          <svg viewBox="0 0 24 24" aria-hidden="true"><path fill="#fff" d="M2 5h20v14H2z"/><path fill="none" stroke="#213f86" stroke-width="2" d="M2 5l10 8 10-8"/></svg>
          info@ridgefellconstruction.com
        </li>
        <li>
          <svg viewBox="0 0 24 24" aria-hidden="true"><circle cx="12" cy="12" r="10" fill="none" stroke="#fff" stroke-width="2"/><path fill="none" stroke="#fff" stroke-width="1.6" d="M2 12h20M12 2c3 3 3 17 0 20M12 2c-3 3-3 17 0 20"/></svg>
          www.ridgefellconstruction.com
        </li>
      </ul>
    </div>
  </section>

  <section class="card card-front" aria-label="Business card, name side">
    <p class="company-name"><span class="company-mark" aria-hidden="true"></span>Ridgefell Construction</p>
  </section>

</main>
</body>
</html>
```